VOMRA Pty Ltd Business Card

Looking for a simple yet eye-catching double-sided business card design using my company logo on one side and contact details on the other.

Target Market(s)

Government

Industry/Entity Type

Communication Systems Engineering

Contact Information for Business Card

VOMRA Pty Ltd

Requirements
Nice to have
• Would be great to have a QR code so details can be scanned into contacts

```html
<!DOCTYPE html>
<html lang="en">
<head>
<meta charset="utf-8">
<title>VOMRA Pty Ltd Business Card</title>
<link rel="stylesheet" href="https://fonts.googleapis.com/css2?family=Open+Sans:wght@400;600;700&display=swap">
<style>
  :root {
    --stage: #232323;
    --slate: #37424b;
    --paper: #ffffff;
    --ink: #1e1e1e;
  }
  * { box-sizing: border-box; margin: 0; padding: 0; }
  html, body { width: 1200px; height: 780px; overflow: hidden; }
  body {
    background: var(--stage);
    font-family: "Open Sans", Arial, sans-serif;
    position: relative;
  }
  .card {
    position: absolute;
    top: 235px;
    width: 540px;
    height: 310px;
    overflow: hidden;
    border-radius: 3px;
  }
  .card--front { left: 40px; background: var(--slate); }
  .card--back { left: 620px; background: var(--slate); }

  .brand {
    position: absolute;
    display: flex;
    align-items: center;
    color: var(--paper);
    font-weight: 700;
    letter-spacing: 0.04em;
  }
  .brand__dot {
    border-radius: 50%;
    border: 3px solid var(--paper);
  }
  .card--front .brand {
    left: 0; right: 0; top: 0; bottom: 0;
    justify-content: center;
    gap: 26px;
    font-size: 76px;
  }
  .card--front .brand__dot { width: 70px; height: 70px; }

  .card--back .brand {
    left: 0; right: 0; top: 34px;
    justify-content: center;
    gap: 16px;
    font-size: 44px;
  }
  .card--back .brand__dot { width: 46px; height: 46px; border-width: 2px; }

  .card__wave { position: absolute; left: 0; top: 0; width: 540px; height: 310px; }

  .holder {
    position: absolute;
    left: 36px;
    top: 148px;
    width: 190px;
    text-align: right;
    color: var(--paper);
  }
  .holder__name { font-size: 23px; font-weight: 700; line-height: 1.1; }
  .holder__role { font-size: 13px; font-weight: 400; margin-top: 2px; }

  .divider {
    position: absolute;
    left: 244px;
    top: 116px;
    width: 2px;
    height: 84px;
    background: var(--paper);
  }

  .contacts {
    position: absolute;
    left: 262px;
    top: 116px;
    list-style: none;
    color: var(--paper);
    font-size: 14.5px;
    line-height: 26px;
  }
  .contacts li { display: flex; align-items: center; gap: 9px; }
  .contacts svg { width: 13px; height: 13px; flex: none; }

  .address {
    position: absolute;
    left: 0; right: 0;
    bottom: 18px;
    text-align: center;
    color: var(--ink);
    font-size: 15px;
    font-weight: 600;
  }
</style>
</head>
<body>

  <section class="card card--front" aria-label="Card front">
    <div class="brand"><span class="brand__dot"></span><span class="brand__name">VOMRA</span></div>
  </section>

  <section class="card card--back" aria-label="Card back">
    <svg class="card__wave" viewBox="0 0 540 310" aria-hidden="true">
      <path d="M0,245 Q330,238 540,198 L540,310 L0,310 Z" fill="var(--paper)"/>
      <path d="M30,258 Q330,250 540,208" fill="none" stroke="var(--slate)" stroke-width="2.5"/>
    </svg>

    <div class="brand"><span class="brand__dot"></span><span class="brand__name">VOMRA</span></div>

    <div class="holder">
      <p class="holder__name">Daniel Hartley</p>
      <p class="holder__role">Co-Founder</p>
    </div>

    <div class="divider"></div>

    <ul class="contacts">
      <li>
        <svg viewBox="0 0 16 16" aria-hidden="true"><path d="M3.6 1.5l2.3 2.6-1.3 1.8c.9 2 2.5 3.6 4.5 4.5l1.8-1.3 2.6 2.3-1.5 2.1C6.9 13.2 2.8 9.1 1.5 3z" fill="var(--paper)"/></svg>
        (817) 555-0148
      </li>
      <li>
        <svg viewBox="0 0 16 16" aria-hidden="true"><circle cx="8" cy="8" r="6.5" fill="none" stroke="var(--paper)" stroke-width="1.4"/><path d="M1.5 8h13M8 1.5c-3 3.5-3 9.5 0 13M8 1.5c3 3.5 3 9.5 0 13" fill="none" stroke="var(--paper)" stroke-width="1.2"/></svg>
        www.vomra.com.au
      </li>
      <li>
        <svg viewBox="0 0 16 16" aria-hidden="true"><rect x="1.5" y="3.5" width="13" height="9" fill="none" stroke="var(--paper)" stroke-width="1.4"/><path d="M1.5 3.5L8 9l6.5-5.5" fill="none" stroke="var(--paper)" stroke-width="1.4"/></svg>
        admin@vomra.com.au
      </li>
    </ul>

    <p class="address">42-44 Harlow Street Redfern NSW 2016 Australia</p>
  </section>

</body>
</html>
```